KRT Flyer to attract applicants 11x17

Lantern Stagehand Collective provides crew for local concerts, filming, theater, and corporate events.
The flyer will be posted on bulletin boards at colleges with theater programs.
Our primary venues are historic theaters in downtown LA
Need a 11x17 poster to attract potential applicants/crew
I have attached a poster that one of our staff made that has all if the relevant info - but i know the poster can look much better than that. I have also attached many images and our logo. It is not necessary to use all of the images, or any of them. The two images of the theater interiors are the venues we operate so they would be the first to include. I can send additional info or images upon request. Thank you

Industry/Entity Type

Entertainment

Requirements
Must have
• APPLY@KRTCREW.EXAMPLE

```html
<!DOCTYPE html>
<html lang="en">
<head>
<meta charset="utf-8">
<title>Lantern Stagehand Collective – Crew Wanted</title>
<link rel="stylesheet" href="https://fonts.googleapis.com/css2?family=Barlow:wght@500;600&family=PT+Sans+Narrow&family=Source+Sans+3:wght@400;600&display=swap">
<style>
  :root {
    --backdrop: #a7a7a7;
    --panel: #3a3b3d;
    --panel-deep: #2f3032;
    --accent: #5eaa84;
    --white: #ffffff;
    --ink-dark: #1f2a24;
    --photo-gold: #c9892f;
    --photo-amber: #8a4a17;
    --photo-brown: #3b2314;
    --photo-green: #4d6a3a;
  }
  * { margin: 0; padding: 0; box-sizing: border-box; }
  html, body { width: 1051px; height: 1200px; overflow: hidden; }
  body {
    background: var(--backdrop);
    font-family: "Source Sans 3", sans-serif;
    position: relative;
  }
  .flyer {
    position: absolute;
    left: 161px; top: 19px;
    width: 728px; height: 1162px;
    overflow: hidden;
    background: var(--panel);
  }
  .venue-photo {
    position: absolute; left: 370px; top: 0; width: 358px; height: 1162px;
    background:
      linear-gradient(180deg, rgba(59,35,20,0.2) 0%, rgba(0,0,0,0) 30%, rgba(77,106,58,0.45) 62%, rgba(59,35,20,0.7) 100%),
      radial-gradient(ellipse at 55% 18%, #e8a640 0%, var(--photo-gold) 30%, var(--photo-amber) 65%, var(--photo-brown) 100%);
  }
  .shapes { position: absolute; inset: 0; width: 728px; height: 1162px; }
  .brand {
    position: absolute; left: 30px; top: 38px;
    display: flex; align-items: center; gap: 12px;
    color: var(--white);
    font-weight: 600; font-size: 20px; letter-spacing: 0.5px; text-transform: uppercase;
  }
  .brand-dot { width: 26px; height: 26px; border-radius: 50%; background: var(--white); }
  .headline {
    position: absolute; left: 52px; top: 412px;
    color: var(--white);
    font-weight: 400; font-size: 70px; line-height: 72px; letter-spacing: 1px;
    text-transform: uppercase;
  }
  .intro {
    position: absolute; left: 52px; top: 614px;
    color: var(--accent); font-size: 33px;
  }
  .role {
    position: absolute; left: 52px; top: 662px;
    color: var(--accent);
    font-family: "PT Sans Narrow", sans-serif;
    font-size: 43px; line-height: 56px; text-transform: uppercase;
  }
  .apply-box {
    position: absolute; left: 233px; top: 954px;
    padding: 7px 12px 8px;
    background: var(--accent); border-radius: 4px;
    color: var(--ink-dark);
    font-family: "Barlow", sans-serif;
  }
  .apply-label { display: block; font-size: 23px; font-weight: 600; letter-spacing: 2.5px; color: var(--white); line-height: 28px; }
  .apply-email { display: block; font-size: 31px; font-weight: 500; line-height: 38px; }
  .website {
    position: absolute; left: 44px; top: 1086px;
    color: var(--white); font-weight: 600; font-size: 24px;
  }
</style>
</head>
<body>
  <main class="flyer">
    <div class="venue-photo" role="img" aria-label="Photograph of an ornate historic theater interior with gilded arches, balconies and rows of seats"></div>

    <svg class="shapes" viewBox="0 0 728 1162" aria-hidden="true">
      <polygon class="panel-fade" points="388,0 430,0 520,560 430,1162 385,1162 472,560" fill="#3a3b3d" opacity="0.45"/>
      <polygon class="panel" points="0,0 388,0 472,560 385,1162 0,1162" fill="#3a3b3d"/>
      <circle class="accent-disc" cx="-35" cy="273" r="133" fill="#5eaa84"/>
      <circle class="accent-ring" cx="196" cy="203" r="15" fill="none" stroke="#5eaa84" stroke-width="9"/>
      <path class="wave" d="M210 320 q11 -10 22 0 t22 0 t22 0 t22 0 t22 0 t22 0 t22 0 t22 0" fill="none" stroke="#ffffff" stroke-width="3"/>
      <g class="arcs" fill="none" stroke="#ffffff" stroke-width="2">
        <path d="M150 850 A150 150 0 0 1 0 1000"/>
        <path d="M141 850 A141 141 0 0 1 0 991"/>
        <path d="M132 850 A132 132 0 0 1 0 982"/>
        <path d="M123 850 A123 123 0 0 1 0 973"/>
        <path d="M114 850 A114 114 0 0 1 0 964"/>
        <path d="M105 850 A105 105 0 0 1 0 955"/>
      </g>
      <g class="dot-grid" fill="#ffffff">
        <g id="dot-row">
          <circle cx="248" cy="0" r="2.3"/><circle cx="270" cy="0" r="2.3"/><circle cx="292" cy="0" r="2.3"/>
          <circle cx="314" cy="0" r="2.3"/><circle cx="336" cy="0" r="2.3"/><circle cx="358" cy="0" r="2.3"/>
          <circle cx="380" cy="0" r="2.3"/><circle cx="402" cy="0" r="2.3"/><circle cx="424" cy="0" r="2.3"/>
          <circle cx="446" cy="0" r="2.3"/><circle cx="468" cy="0" r="2.3"/>
        </g>
        <use href="#dot-row" y="924"/>
        <use href="#dot-row" y="944"/>
        <use href="#dot-row" y="1048"/>
        <use href="#dot-row" y="1068"/>
      </g>
    </svg>

    <div class="brand"><span class="brand-dot"></span><span class="brand-name">Lantern Stagehand Collective</span></div>

    <h1 class="headline">Has open<br>position</h1>
    <p class="intro">We are looking for</p>
    <p class="role">Talented lighting and<br>sound technicians</p>

    <div class="apply-box">
      <span class="apply-label">Send resume to:</span>
      <span class="apply-email">APPLY@KRTCREW.EXAMPLE</span>
    </div>

    <p class="website">www.krtcrew.example</p>
  </main>
</body>
</html>
```